Looking for a dynamic business card for a pizzeria.

A business card with our food, logo, and space for name, title, email, website, phone. The card should convey quality, unique, amazing. On the front, I envision food photo or photos with the owners names and contact information. On the back, more food with locations, website, facebook, twitter, instagram icons. It should look polished, not cartoonish, or plain.
Target Market(s)
upscale, local food buyers, 30-50 years in age.
Industry/Entity Type
Restaurant
Contact Information for Business Card
Business Name: Bru'nettix, LLC
Website: www.brunettix.com
Back:
2 locations: (can list on the back of card)
1. Harborview
4087 Corlan Avenue
Marrowport, WA 98310
360-481-5067
2. Cedar Ridge
7315 Wendmere Road
Marrowport, WA 98314
360-293-8840
front:
EDITABLE space for
Business name
Person's Name
title
2nd title
Email address
cell-phone number
Requirements
Must have
- logo
- my food photo or photos (no watermarks showing)
- locations on back
- Person contact information on front
- full bleed

```html
<!DOCTYPE html>
<html lang="en">
<head>
<meta charset="utf-8">
<title>Bru'nettix, LLC — Business Card</title>
<link rel="stylesheet" href="https://fonts.googleapis.com/css2?family=Arimo:wght@400;700&display=swap">
<style>
  :root {
    --stage: #e8e3db;
    --card: #ffffff;
    --card-edge: #f1efec;
    --green: #1f6a2f;
    --red: #c5232c;
    --red-dark: #9c1a21;
    --ink: #333333;
    --rule: #2a2a2a;
  }
  * { box-sizing: border-box; margin: 0; padding: 0; }
  html, body {
    width: 1200px; height: 780px; overflow: hidden;
    background: var(--stage);
    font-family: "Arimo", Arial, sans-serif;
  }
  .stage { position: relative; width: 1200px; height: 780px; }

  .card {
    position: absolute;
    width: 540px; height: 310px;
    background: linear-gradient(160deg, var(--card), var(--card-edge));
    box-shadow: 0 8px 24px rgba(0,0,0,.18);
    overflow: hidden;
  }
  .card--front { left: 40px; top: 70px; }
  .card--back  { left: 620px; top: 400px; }

  .card__art { position: absolute; inset: 0; width: 540px; height: 310px; }

  .card__content { position: absolute; }

  /* Front */
  .front__content { left: 300px; top: 26px; width: 220px; }
  .brand { display: flex; align-items: center; gap: 10px; margin-bottom: 44px; }
  .brand__dot { width: 26px; height: 26px; border-radius: 50%; background: var(--red); flex: none; }
  .brand__name { font-size: 30px; font-weight: 400; color: var(--green); letter-spacing: 0.5px; }
  .person__name { font-size: 22px; font-weight: 700; color: var(--green); }
  .person__title { font-size: 14px; color: var(--red); margin: 2px 0 12px; }
  .contact { list-style: none; font-size: 14px; color: var(--red); }
  .contact li { display: flex; align-items: center; gap: 8px; margin-bottom: 5px; }
  .contact__icon {
    width: 16px; height: 16px; background: var(--green); border-radius: 2px;
    display: flex; align-items: center; justify-content: center; flex: none;
  }
  .contact__web { color: var(--green); margin-top: 6px; }

  /* Back */
  .back__content { left: 300px; top: 22px; width: 225px; }
  .company { font-size: 24px; font-weight: 400; color: var(--green); letter-spacing: 1px; margin-bottom: 14px; text-transform: uppercase; }
  .location__name { font-size: 13px; font-weight: 700; color: var(--green); text-transform: uppercase; }
  .location__addr { font-size: 13.5px; color: var(--ink); line-height: 1.3; }
  .location__phone { font-size: 14px; color: var(--red); margin-top: 2px; }
  .location-rule { border: 0; border-top: 1.5px solid var(--rule); width: 185px; margin: 10px 0; }
</style>
</head>
<body>
<main class="stage">

  <section class="card card--front" aria-label="Business card front">
    <svg class="card__art" viewBox="0 0 540 310">
      <defs>
        <linearGradient id="front-photo" x1="0" y1="0" x2="1" y2="1">
          <stop offset="0" stop-color="#e9e3b8"/>
          <stop offset="0.35" stop-color="#8fbf3e"/>
          <stop offset="0.65" stop-color="#7a4a36"/>
          <stop offset="1" stop-color="#efe6d4"/>
        </linearGradient>
        <linearGradient id="swoosh" x1="0" y1="0" x2="0" y2="1">
          <stop offset="0" stop-color="#c5232c"/>
          <stop offset="1" stop-color="#9c1a21"/>
        </linearGradient>
      </defs>
      <path role="img" aria-label="Food photo: roast beef sandwich with green peppers and red onion"
            d="M0 0 H240 C300 90 230 230 300 310 H0 Z" fill="url(#front-photo)"/>
      <path d="M240 0 C300 90 230 230 300 310" fill="none" stroke="url(#swoosh)" stroke-width="9"/>
      <path d="M252 0 C312 90 242 230 312 310" fill="none" stroke="#c5232c" stroke-width="1.5" opacity=".5"/>
    </svg>
    <div class="card__content front__content">
      <div class="brand">
        <span class="brand__dot"></span>
        <span class="brand__name">Bru'nettix</span>
      </div>
      <p class="person__name">Employee Name</p>
      <p class="person__title">Managing Director</p>
      <ul class="contact">
        <li>
          <span class="contact__icon">
            <svg width="10" height="12" viewBox="0 0 10 12"><rect x="1" y="0.5" width="8" height="11" rx="1.5" fill="none" stroke="#fff" stroke-width="1.2"/><rect x="3" y="2.5" width="4" height="4" fill="#fff"/></svg>
          </span>123 456 7890
        </li>
        <li>
          <span class="contact__icon">
            <svg width="12" height="9" viewBox="0 0 12 9"><rect x="0.6" y="0.6" width="10.8" height="7.8" fill="none" stroke="#fff" stroke-width="1.2"/><path d="M0.6 0.6 L6 5 L11.4 0.6" fill="none" stroke="#fff" stroke-width="1.2"/></svg>
          </span>you@yourmail.com
        </li>
        <li class="contact__web">www.brunettix.com</li>
      </ul>
    </div>
  </section>

  <section class="card card--back" aria-label="Business card back">
    <svg class="card__art" viewBox="0 0 540 310">
      <defs>
        <linearGradient id="back-photo" x1="0" y1="0" x2="1" y2="1">
          <stop offset="0" stop-color="#e7c9b3"/>
          <stop offset="0.4" stop-color="#c45a3c"/>
          <stop offset="0.7" stop-color="#e9ddd0"/>
          <stop offset="1" stop-color="#d9a88e"/>
        </linearGradient>
        <linearGradient id="swoosh-back" x1="0" y1="0" x2="0" y2="1">
          <stop offset="0" stop-color="#c5232c"/>
          <stop offset="1" stop-color="#9c1a21"/>
        </linearGradient>
      </defs>
      <path role="img" aria-label="Food photo: pepperoni sandwich on a plate"
            d="M0 0 H240 C300 90 230 230 300 310 H0 Z" fill="url(#back-photo)"/>
      <path d="M240 0 C300 90 230 230 300 310" fill="none" stroke="url(#swoosh-back)" stroke-width="9"/>
      <path d="M252 0 C312 90 242 230 312 310" fill="none" stroke="#c5232c" stroke-width="1.5" opacity=".5"/>
    </svg>
    <div class="card__content back__content">
      <h1 class="company">Bru'nettix, LLC</h1>
      <div class="location">
        <p class="location__name">Harborview</p>
        <p class="location__addr">4087 Corlan Avenue<br>Marrowport, WA 98310</p>
        <p class="location__phone">360-481-5067</p>
      </div>
      <hr class="location-rule">
      <div class="location">
        <p class="location__name">Cedar Ridge</p>
        <p class="location__addr">7315 Wendmere Road<br>Marrowport, WA 98314</p>
        <p class="location__phone">360-293-8840</p>
      </div>
    </div>
  </section>

</main>
</body>
</html>
```